Paperwell Solutions Services Flyer

Create a 2 sided A4 flyer/PDF of the services we offer and a description of each etc.
Details can be found at: https://www.paperwell-solutions.co.uk/
Main services: Document Scanning, Invoice Processing and other services we offer.

Industry/Entity Type

Document Management

Font styles to use
Other font styles liked:
• Montserrat

Colors

Designer to choose colors to be used in the design.

Requirements
Must have
• Document Scanning, Box Storage, Invoice Processing, Book Scanning, Large format scanning
Nice to have
• Colourful d/s flyer listing our services with a brief description on each

```html
<!DOCTYPE html>
<html lang="en">
<head>
<meta charset="utf-8">
<title>Paperwell Solutions – Services Flyer</title>
<link href="https://fonts.googleapis.com/css2?family=Montserrat:wght@400;500;600;700&display=swap" rel="stylesheet">
<style>
:root{
  --red:#c8161d;
  --red-dark:#8e0d12;
  --ink:#3a3a3a;
  --muted:#6b6b6b;
  --paper:#f4f4f4;
  --stage:#e6e6e6;
  --white:#ffffff;
}
*{box-sizing:border-box;margin:0;padding:0}
html,body{width:1200px;height:848px;overflow:hidden;background:var(--stage);font-family:"Montserrat",sans-serif;color:var(--ink)}
.canvas{position:relative;width:1200px;height:848px}
.page{position:absolute;top:42px;width:540px;height:764px;background:var(--paper);overflow:hidden;box-shadow:0 6px 20px rgba(0,0,0,.18)}
.page--front{left:40px}
.page--back{left:620px}
.side-url{position:absolute;writing-mode:vertical-rl;font-size:9px;letter-spacing:6px;color:var(--muted);text-transform:lowercase}
.side-url--left{left:12px}
.side-url--right{right:12px}

/* front */
.hero{position:absolute;left:0;top:0;width:540px;height:290px;background:linear-gradient(135deg,#2a3350 0%,#5a2440 55%,#b8243a 100%)}
.hero-swoosh{position:absolute;left:0;top:190px;width:540px;height:130px}
.brand{position:absolute;left:26px;top:0;width:150px;height:66px;background:var(--white);border-radius:0 0 12px 12px;display:flex;align-items:center;justify-content:center;text-align:center;color:var(--red);font-weight:700;font-size:17px;line-height:1.05}
.hero-title{position:absolute;left:24px;top:92px;width:500px;color:var(--white);font-weight:700;font-size:25px;letter-spacing:.3px;text-shadow:0 2px 6px rgba(0,0,0,.35)}
.product{position:absolute;top:146px;width:72px;height:72px;border-radius:50%;border:3px solid var(--white);background:radial-gradient(circle at 40% 35%,#f2f2f2,#9a9ea6)}
.contact-btn{position:absolute;left:216px;top:170px;padding:6px 14px;border:1.5px solid var(--white);border-radius:14px;background:rgba(20,24,40,.55);color:var(--white);font-size:9px;font-weight:600;letter-spacing:.5px}
.ribbon{position:absolute;left:50px;top:282px;width:440px;height:38px;background:var(--red);color:var(--white);font-weight:600;font-size:17px;letter-spacing:.4px;display:flex;align-items:center;justify-content:center;border-radius:8px 8px 0 0}
.grid{position:absolute;left:60px;top:330px;display:grid;grid-template-columns:repeat(3,130px);grid-auto-rows:106px;gap:12px 15px}
.card{background:var(--white);border:1.5px solid var(--red);border-radius:10px;display:flex;flex-direction:column;align-items:center;justify-content:center;gap:6px;text-align:center;padding:6px}
.card-icon{width:40px;height:40px;border-radius:8px;background:linear-gradient(135deg,#3c5a78,#c8161d)}
.card-name{color:var(--red);font-weight:700;font-size:12.5px;line-height:1.05}
.footer-swoosh{position:absolute;left:0;top:674px;width:540px;height:90px;z-index:0}
.footer-info{position:relative;z-index:1}
.contact-list{position:absolute;left:60px;top:684px;font-size:8.5px;color:var(--ink);line-height:1.9}
.contact-list span{display:flex;align-items:center;gap:6px}
.address{position:absolute;left:210px;top:684px;font-size:8.5px;line-height:1.35;display:flex;gap:6px}
.certs{position:absolute;left:356px;top:682px;text-align:center}
.cert-badges{display:flex;gap:10px;justify-content:center;margin-bottom:6px}
.cert-badge{width:24px;height:24px;border-radius:50%;border:1.5px solid #888}
.cert-badge--square{border-radius:3px}
.cert-text{font-size:7.5px;color:var(--red-dark);font-weight:600;line-height:1.4}

/* back */
.back-hero{position:absolute;left:0;top:0;width:540px;height:150px;background:linear-gradient(135deg,#232a3d 0%,#3d3550 60%,#6b2a44 100%)}
.back-hero-copy{position:absolute;left:40px;top:20px;width:460px;text-align:center;color:var(--white)}
.back-title{font-size:22px;font-weight:700;margin-bottom:8px}
.back-intro{font-size:9px;line-height:1.45}
.service-list{position:absolute;left:48px;top:164px;width:444px;display:flex;flex-direction:column;gap:10px}
.service-group{border:1.5px solid var(--red);border-radius:12px;padding:6px 14px;display:flex;flex-direction:column;gap:5px}
.service{display:flex;gap:12px;align-items:center}
.service-icon{flex:none;width:34px;height:34px;border-radius:50%;border:1.5px solid var(--red);background:radial-gradient(circle,#3c5a78 30%,#fff 32%)}
.service-name{color:var(--red);font-weight:700;font-size:12.5px;margin-bottom:1px}
.service-desc{font-size:7.4px;line-height:1.35;color:var(--muted)}
</style>
</head>
<body>
<div class="canvas">

  <section class="page page--front">
    <div class="hero" role="img" aria-label="Photo of two technicians in lab coats working at a laptop in a records archive"></div>
    <svg class="hero-swoosh" viewBox="0 0 540 130" preserveAspectRatio="none" aria-hidden="true">
      <path d="M0 40 C120 110 300 120 540 60 L540 130 L0 130 Z" fill="var(--red)"/>
      <path d="M0 70 C140 125 320 130 540 80 L540 130 L0 130 Z" fill="var(--paper)"/>
      <path d="M0 60 C140 118 320 122 540 72" stroke="var(--white)" stroke-width="3" fill="none"/>
    </svg>
    <div class="brand">Paperwell<br>Solutions</div>
    <h1 class="hero-title">Document Automation Services</h1>
    <div class="product" style="left:36px" role="img" aria-label="Scanner workstation"></div>
    <div class="product" style="left:122px" role="img" aria-label="Desktop document scanner"></div>
    <div class="contact-btn">CONTACT US</div>
    <div class="product" style="left:346px" role="img" aria-label="Production scanner"></div>
    <div class="product" style="left:432px" role="img" aria-label="Large format scanner"></div>

    <div class="ribbon">What can we do for you?</div>
    <div class="grid">
      <div class="card"><div class="card-icon" role="img" aria-label="Scanning icon"></div><div class="card-name">Document<br>Scanning</div></div>
      <div class="card"><div class="card-icon" role="img" aria-label="Processing icon"></div><div class="card-name">Document<br>Processing</div></div>
      <div class="card"><div class="card-icon" role="img" aria-label="Storage box icon"></div><div class="card-name">Box<br>Storage</div></div>
      <div class="card"><div class="card-icon" role="img" aria-label="Shredding icon"></div><div class="card-name">Secure<br>Document<br>Destruction</div></div>
      <div class="card"><div class="card-icon" role="img" aria-label="Folder icon"></div><div class="card-name">Document<br>Management<br>Systems</div></div>
      <div class="card"><div class="card-icon" role="img" aria-label="Digital mail icon"></div><div class="card-name">Digital<br>Mailroom</div></div>
      <div class="card"><div class="card-icon" role="img" aria-label="Film reel icon"></div><div class="card-name">Microfilm<br>Digitisation</div></div>
      <div class="card"><div class="card-icon" role="img" aria-label="Gears icon"></div><div class="card-name">Workflow<br>Systems</div></div>
      <div class="card"><div class="card-icon" role="img" aria-label="Large document icon"></div><div class="card-name">Large Format<br>Scanning</div></div>
    </div>

    <svg class="footer-swoosh" viewBox="0 0 540 90" preserveAspectRatio="none" aria-hidden="true">
      <path d="M0 66 C140 74 300 82 470 90 L440 90 C300 84 140 80 0 74 Z" fill="var(--red)"/>
      <path d="M0 80 C100 84 200 88 300 90 L0 90 Z" fill="var(--red)"/>
      <path d="M470 90 C505 80 530 55 540 22 L540 90 Z" fill="var(--red)"/>
    </svg>
    <div class="footer-info">
      <div class="contact-list">
        <span><svg width="9" height="9" viewBox="0 0 24 24"><path fill="var(--red)" d="M6.6 10.8a15 15 0 0 0 6.6 6.6l2.2-2.2a1 1 0 0 1 1-.25 11 11 0 0 0 3.6.6 1 1 0 0 1 1 1V20a1 1 0 0 1-1 1A17 17 0 0 1 3 4a1 1 0 0 1 1-1h3.5a1 1 0 0 1 1 1 11 11 0 0 0 .6 3.6 1 1 0 0 1-.25 1z"/></svg>01632 480215</span>
        <span><svg width="9" height="9" viewBox="0 0 24 24"><path fill="var(--red)" d="M2 5h20v14H2z M2 5l10 8 10-8" stroke="#fff" stroke-width="1.5"/></svg>sales@paperwell.co.uk</span>
      </div>
      <div class="address">
        <svg width="9" height="11" viewBox="0 0 24 30"><path fill="var(--red)" d="M12 0a10 10 0 0 0-10 10c0 8 10 20 10 20s10-12 10-20A10 10 0 0 0 12 0zm0 14a4 4 0 1 1 0-8 4 4 0 0 1 0 8z"/></svg>
        <span>Marlow Court,<br>Fenwick Road,<br>Ashby, North Downs<br>AB12 3CD</span>
      </div>
      <div class="certs">
        <div class="cert-badges"><div class="cert-badge"></div><div class="cert-badge cert-badge--square"></div><div class="cert-badge"></div></div>
        <div class="cert-text">Certificate No. 20480<br>ISO 9001 ISO 27001</div>
      </div>
    </div>
    <div class="side-url side-url--left" style="top:330px">paperwell-solutions.co.uk</div>
    <div class="side-url side-url--right" style="top:360px">paperwell-solutions.co.uk</div>
  </section>

  <section class="page page--back">
    <div class="back-hero" role="img" aria-label="Dim photo of archive shelving with files"></div>
    <div class="back-hero-copy">
      <h2 class="back-title">Document Automation Services</h2>
      <p class="back-intro">At Paperwell Solutions, we deliver award-winning document automation services, from business process optimisation and document management to data capture and document scanning. We specialise in transforming your most labour-intensive workflows into cost-effective automated solutions, helping you save money, enhance efficiency and grow your business.</p>
    </div>

    <div class="service-list">
      <div class="service-group">
        <div class="service"><div class="service-icon" role="img" aria-label="Scanning icon"></div><div><div class="service-name">Document Scanning</div><p class="service-desc">Digitise your physical files with high-volume scanning. We convert paper records into digital formats such as PDF, keeping information accessible.</p></div></div>
        <div class="service"><div class="service-icon" role="img" aria-label="Processing icon"></div><div><div class="service-name">Document Processing</div><p class="service-desc">Streamline operations with customised processing. Automation replaces manual workflows, reduces human error and saves time and cost.</p></div></div>
        <div class="service"><div class="service-icon" role="img" aria-label="Storage box icon"></div><div><div class="service-name">Box Storage</div><p class="service-desc">Secure your critical records in regulated facilities and robust cloud platforms, ensuring reliable retention of physical and digital records.</p></div></div>
      </div>

      <div class="service-group">
        <div class="service"><div class="service-icon" role="img" aria-label="Shredding icon"></div><div><div class="service-name">Secure Document Destruction</div><p class="service-desc">Dispose of obsolete or sensitive documents securely with certified destruction, in line with stringent regulatory requirements.</p></div></div>
        <div class="service"><div class="service-icon" role="img" aria-label="Folder icon"></div><div><div class="service-name">Document Management Systems</div><p class="service-desc">Centralise your information in one searchable repository with feature-rich software, improving access and productivity.</p></div></div>
        <div class="service"><div class="service-icon" role="img" aria-label="Digital mail icon"></div><div><div class="service-name">Digital Mailroom</div><p class="service-desc">Future-proof your business: we digitise incoming mail and automate workflows, replacing outdated paper-based systems.</p></div></div>
      </div>

      <div class="service-group">
        <div class="service"><div class="service-icon" role="img" aria-label="Film reel icon"></div><div><div class="service-name">Microfilm Digitisation</div><p class="service-desc">Preserve historical data by converting microfilm records into searchable, high-quality digital formats for lasting usability.</p></div></div>
        <div class="service"><div class="service-icon" role="img" aria-label="Gears icon"></div><div><div class="service-name">Workflow Systems</div><p class="service-desc">Tailored workflow systems automate tasks, reduce manual steps and enable seamless information flow across your organisation.</p></div></div>
        <div class="service"><div class="service-icon" role="img" aria-label="Large document icon"></div><div><div class="service-name">Large Format Scanning</div><p class="service-desc">Specialised large-format scanning digitises blueprints, maps and posters with precision and clarity, so no detail is lost.</p></div></div>
      </div>

      <div class="service-group">
        <div class="service"><div class="service-icon" role="img" aria-label="Invoice icon"></div><div><div class="service-name">Invoice Processing</div><p class="service-desc">Capture, validate and route supplier invoices automatically, cutting manual data entry and speeding up approval and payment.</p></div></div>
        <div class="service"><div class="service-icon" role="img" aria-label="Book icon"></div><div><div class="service-name">Book Scanning</div><p class="service-desc">Careful, non-destructive scanning of bound books, ledgers and registers into clear, searchable digital copies.</p></div></div>
      </div>
    </div>

    <div class="side-url side-url--left" style="top:300px">paperwell-solutions.co.uk</div>
    <div class="side-url side-url--right" style="top:340px">paperwell-solutions.co.uk</div>
  </section>

</div>
</body>
</html>
```